digger and truck hire

this is a new business - Digger and Truck
we would like to include the attached photo of the digger and truck - as the truck is red and the digger is green
maybe either black or white lettering which ever suits

Industry/Entity Type

Business

Contact Information for Business Card

RDL - Brodie's 2.5t Mini Digger and 7t Tip Truck -Hire, full attachments, augers, trenching, site preparation, small aggregate deliveries
Phone 0218365904
brodie.rdl@fernmail.co.nz

```html
<!DOCTYPE html>
<html lang="en">
<head>
<meta charset="utf-8">
<title>RDL – Business Card</title>
<link rel="stylesheet" href="https://fonts.googleapis.com/css2?family=Didact+Gothic&display=swap">
<style>
  :root {
    --orange: #e2461f;
    --ink: #111111;
    --white: #ffffff;
    --page: #ececec;
    --photo-sky: #dfe6ec;
    --photo-steel: #c9d1d8;
    --photo-truck: #e9b9a6;
    --photo-digger: #cdd3c9;
  }
  * { box-sizing: border-box; margin: 0; padding: 0; }
  html, body {
    width: 1200px; height: 1200px; overflow: hidden;
    background: var(--page);
    font-family: "Didact Gothic", "Century Gothic", sans-serif;
  }
  .business-card {
    position: absolute; left: 100px; top: 314px;
    width: 1000px; height: 571px;
    background: var(--white);
    overflow: hidden;
    box-shadow: 0 6px 18px rgba(0,0,0,.25);
  }
  .card-photo {
    position: absolute; left: 0; top: 118px; width: 1000px; height: 453px;
    background:
      linear-gradient(90deg, var(--photo-truck) 0%, rgba(233,185,166,0) 45%),
      linear-gradient(180deg, var(--photo-sky) 0%, var(--photo-steel) 45%, var(--photo-digger) 70%, var(--photo-truck) 100%);
    opacity: .75;
  }
  .brand-name {
    position: absolute; left: 30px; top: 6px;
    font-size: 108px; line-height: 1; color: var(--ink); letter-spacing: 2px;
  }
  .tagline {
    position: absolute; left: 275px; top: 66px;
    font-size: 28px; color: var(--ink); letter-spacing: .5px; text-transform: uppercase;
  }
  .header-rule {
    position: absolute; left: 30px; top: 110px; width: 970px; height: 8px;
    background: var(--orange);
  }
  .services {
    position: absolute; left: 36px; top: 168px; list-style: none;
  }
  .services li {
    display: flex; align-items: center; height: 48px;
    font-size: 31px; color: var(--ink);
  }
  .services li::before {
    content: ""; width: 14px; height: 14px; border-radius: 50%;
    background: var(--orange); margin: 0 16px 0 8px;
  }
  .contact {
    position: absolute; left: 514px; display: flex; align-items: center;
    font-size: 33px; color: var(--ink);
  }
  .contact svg { width: 58px; height: 58px; margin-right: 22px; }
  .contact-phone { top: 163px; }
  .contact-email { top: 254px; }
  .footer-band { position: absolute; left: 0; top: 0; }
  .footer-name {
    position: absolute; right: 62px; top: 466px;
    font-size: 100px; line-height: 1; color: var(--white); letter-spacing: 4px;
  }
</style>
</head>
<body>
  <div class="business-card">
    <div class="card-photo" role="img" aria-label="Photo of the green mini digger strapped onto the red tip truck"></div>

    <div class="brand-name">RDL</div>
    <div class="tagline">Brodie's 2.5t Mini Digger and 7t Tip Truck-Hire</div>
    <div class="header-rule"></div>

    <ul class="services">
      <li>Full Attachment</li>
      <li>Augers</li>
      <li>Trenching</li>
      <li>Site Preparation</li>
      <li>Small Aggregate Deliveries</li>
    </ul>

    <div class="contact contact-phone">
      <svg viewBox="0 0 58 58" aria-hidden="true">
        <circle cx="29" cy="29" r="26" fill="none" stroke="var(--orange)" stroke-width="3"/>
        <path d="M21 16c2-1 4 0 5 2l2 5c1 2 0 3-1 4l-2 2c2 4 5 7 9 9l2-2c1-1 2-2 4-1l5 2c2 1 3 3 2 5l-1 2c-2 2-6 3-10 1-8-4-14-10-18-18-2-4-1-8 1-10z" fill="var(--orange)"/>
      </svg>
      <span>0218365904</span>
    </div>
    <div class="contact contact-email">
      <svg viewBox="0 0 58 58" aria-hidden="true">
        <circle cx="29" cy="29" r="26" fill="none" stroke="var(--orange)" stroke-width="3"/>
        <rect x="15" y="19" width="28" height="20" fill="none" stroke="var(--orange)" stroke-width="2.5"/>
        <path d="M15 19l14 12 14-12M15 39l10-10M43 39l-10-10" fill="none" stroke="var(--orange)" stroke-width="2.5"/>
      </svg>
      <span>brodie.rdl@fernmail.co.nz</span>
    </div>

    <svg class="footer-band" width="1000" height="571" viewBox="0 0 1000 571" aria-hidden="true">
      <polygon points="0,524 420,524 480,460 1000,460 1000,571 0,571" fill="var(--orange)"/>
    </svg>
    <div class="footer-name">RDL</div>
  </div>
</body>
</html>
```